Web Design Project for Communications Agency

The design I need (PSD file) is for an agency offering specialised PR and communications services for customers in the healthcare sector.

OBJECTIVES OF THE WEBSITE:
1. To promote the agency's communication services
2. To position Solène Brivard as an industry leader, an expert in healthcare PR and communications by highlighting blogposts and social media.

WHAT I NEED:
1st, I need the design for the Home Page ONLY.
Once approved, I will need the other pages designed as well. (Here is prototype that we've already developed for the Website that will guide you in the design:
http://qorvelle.net/solenebrivard/)

VISUAL INSPIRATION
We want to give this Website a "Flat Design" look. Here are some websites for inspiration :
- http://tavrolinkworks.com/#!/process
- http://www.brindlemoss.co/
- http://quellaroft.com/

Also, reuse images found on the company's current Website :
http://www.solenebrivard.com/fr/index.html

HOMEPAGE MAIN ELEMENTS:
1. Main menu : 6 sections
Accueil | Agence | Services | Approche | Publications | Contact

2. Main Call To Action (big dark rectangle in prototype):
Can be slider or just an information bloc.

3. Publications récentes :
The 4 latest blog posts must be features on the homepage (will be linked with the "Publications" section)

4. Dynamic Footer :
Contains a Chirpline feed and a Subscribe to our Newsletter feature (revecez nos publications)

OTHER PAGES (to design once Homepage is approved)
- Agence (about us)
- Services (our team)
- Approche (our approach)
- Publications (blog articles)
- Contact (Contact us)

Industry/Entity Type

Communications

Requirements
Must have
• Please refer to prototype :
http://qorvelle.net/solenebrivard/
Must have ALL features present in prototype.

Also, must reuse this picture in the design : http://solenebrivard.com/static/images/home-big-box.jpg

Finally, you will find attached the company logo.

```html
<!DOCTYPE html>
<html lang="fr">
<head>
<meta charset="utf-8">
<title>Solène Brivard — Accueil</title>
<link rel="stylesheet" href="https://fonts.googleapis.com/css2?family=Open+Sans:wght@400;600;700&family=Lato:wght@400;700&family=Roboto+Condensed:wght@700&family=Arimo:wght@400;700&display=swap">
<style>
:root{
  --red:#e8343a;
  --red-dark:#d42d33;
  --accent:#d9333b;
  --ink:#111;
  --topbar:#0a0a0a;
  --header:#f7f7f7;
  --card:#f3f3f3;
  --muted:#6e6e6e;
  --footer:#2b2b2b;
  --footer-bottom:#222;
  --field:#444;
  --salmon:#f05a5a;
  --sky:#2eb7e6;
  --hero-box:#4b4b4b;
}
*{margin:0;padding:0;box-sizing:border-box}
html,body{width:1200px;height:2639px;overflow:hidden;background:#fff}
body{position:relative;font-family:"Open Sans",Arial,sans-serif;color:var(--ink)}
.abs{position:absolute}

/* top bar */
.topbar{left:0;top:0;width:1200px;height:30px;background:var(--topbar);color:#fff;font:700 13px/30px "Arimo",Arial,sans-serif}
.topbar .welcome{left:123px}
.topbar .lang{left:934px}
.topbar .lang em{font-style:italic;margin-left:6px}
.topbar-stripe{left:0;top:28px;width:1200px;height:3px;background:linear-gradient(90deg,#e8343a,#f3a33a,#8cc63f,#2eb7e6,#9b59b6,#e8343a)}

/* header */
.site-header{left:0;top:31px;width:1200px;height:127px;background:var(--header);box-shadow:0 2px 4px rgba(0,0,0,.08)}
.brand{left:123px;top:44px;display:flex;align-items:center;gap:12px}
.brand-mark{width:18px;height:18px;background:var(--red)}
.brand-name{font:700 36px/1 "Roboto Condensed",Arial,sans-serif;color:var(--red)}
.social-top{top:24px;display:flex;gap:11px;left:977px}
.social-top span{width:26px;height:26px;border-radius:3px;background:#3aa9e0;display:block}
.main-nav{top:74px;left:519px;display:flex;font-size:17px;color:#111}
.main-nav a{color:inherit;text-decoration:none;position:absolute;white-space:nowrap}

/* hero */
.hero{left:0;top:158px;width:1200px;height:611px;background:linear-gradient(90deg,#f4f6f8 0%,#e9eef2 40%,#d4e4ef 62%,#bcd2e4 80%,#e4ecf2 100%)}
.hero-cube{left:170px;top:100px;width:300px;height:300px;background:radial-gradient(circle at 50% 45%,#f4f4f4 0%,#dcdcdc 55%,rgba(240,240,240,0) 72%)}
.hero-team{left:620px;top:0;width:580px;height:611px;background:linear-gradient(180deg,#eaf0f5 0%,#c9dbea 50%,#9fbdd6 100%)}
.hero-lines{left:120px;top:424px}
.hero-lines span{display:table;background:var(--hero-box);color:#fff;font:400 27px/38px "Arimo",Arial,sans-serif;padding:0 12px;margin-bottom:4px}
.hero-cta{left:120px;top:551px;width:183px;height:37px;background:var(--red);color:#fff;font:700 17px/37px "Arimo",Arial,sans-serif;text-align:center}

/* publications heading */
.pub-head{left:0;top:769px;width:1200px;height:146px;text-align:center}
.pub-head h2{position:absolute;left:0;top:34px;width:100%;font:700 42px/1 "Roboto Condensed",Arial,sans-serif}
.pub-head p{position:absolute;left:0;top:98px;width:100%;font-size:15px;color:var(--red)}

/* publications list */
.pub-list{left:0;top:915px;width:1200px;height:1149px;background:var(--red)}
.post{position:absolute;left:109px;width:982px;height:211px}
.post-photo{position:absolute;left:0;top:0;width:334px;height:211px}
.post-body{position:absolute;left:345px;top:0;width:637px;height:211px;background:var(--card);box-shadow:0 1px 2px rgba(0,0,0,.2);padding:20px 19px 0 21px}
.post-body::before{content:"";position:absolute;left:-22px;top:86px;border:13px solid transparent;border-right-color:var(--card);border-width:13px 11px}
.post-title{font:400 23px/1.2 "Open Sans",Arial,sans-serif;color:#111}
.post-date{font-size:12px;color:var(--red);margin-top:1px}
.post-text{font-size:13px;line-height:20px;color:var(--muted);margin-top:6px}
.post-more{position:absolute;left:21px;top:169px;width:150px;height:22px;background:#000;color:#fff;font:700 12px/22px "Open Sans",Arial,sans-serif;text-align:center}
.divider{position:absolute;left:202px;width:796px;border-top:2px dotted rgba(255,255,255,.45)}

/* footer */
.site-footer{left:0;top:2064px;width:1200px;height:514px;background:var(--footer);font-family:"Lato",Arial,sans-serif}
.site-footer h3{position:absolute;left:0;top:24px;width:100%;text-align:center;color:#fff;font:700 26px/1.2 "Lato",Arial,sans-serif}
.touch-text{position:absolute;left:132px;top:67px;width:942px;text-align:center;color:#8d8d8d;font-size:17px;line-height:27px}
.newsletter-title{position:absolute;left:132px;top:154px;color:#fff;font:700 19px/1 "Arimo",Arial,sans-serif}
.field{position:absolute;left:132px;width:581px;height:32px;background:var(--field);color:#8a8a8a;font-size:13px;line-height:32px;padding-left:8px}
.submit{position:absolute;left:132px;top:305px;width:81px;height:30px;background:var(--salmon);border-radius:3px;color:#fff;font:700 10px/30px "Lato",Arial,sans-serif;letter-spacing:1px;text-align:center}
.col-title{position:absolute;top:366px;color:#fff;font:700 17px/1 "Lato",Arial,sans-serif}
.col-text{position:absolute;color:#aaa;font-size:12px;line-height:20px}
.contact-line{position:absolute;left:132px;color:#aaa;font-size:12px;display:flex;align-items:center;gap:8px}
.net-icons{position:absolute;left:426px;top:462px;display:flex;gap:7px}
.net-icons span{width:25px;height:25px;border-radius:50%;display:block}
.feed-name{position:absolute;left:746px;top:214px;color:var(--sky);font:700 54px/1 "Lato",Arial,sans-serif}
.tweet{position:absolute;left:746px;width:330px;color:#bbb;font-size:12px;line-height:18px}
.tweet b{color:var(--salmon);font-weight:400}
.footer-bottom{left:0;top:2578px;width:1200px;height:61px;background:var(--footer-bottom);color:#888;font:400 12px/61px "Lato",Arial,sans-serif;text-align:center}
.footer-bottom strong{color:#ccc;font-weight:400}
</style>
</head>
<body>

<div class="abs topbar">
  <span class="abs welcome">Welcome to Solène Brivard ...</span>
  <span class="abs lang">Language : <em>English</em></span>
</div>
<div class="abs topbar-stripe"></div>

<header class="abs site-header">
  <div class="abs brand"><span class="brand-mark"></span><span class="brand-name">Solène Brivard</span></div>
  <div class="abs social-top" aria-label="Réseaux sociaux"><span></span><span></span><span></span></div>
  <nav class="abs main-nav">
    <a style="left:0">Accueil</a>
    <a style="left:88px">Agence</a>
    <a style="left:180px">Services</a>
    <a style="left:278px">Approche</a>
    <a style="left:389px">Publications</a>
    <a style="left:516px">Contact</a>
  </nav>
</header>

<section class="abs hero">
  <div class="abs hero-team" role="img" aria-label="Photo d'une équipe médicale souriante en blouse blanche"></div>
  <div class="abs hero-cube" role="img" aria-label="Cube blanc orné d'une croix rouge"></div>
  <div class="abs hero-lines">
    <span>Cabinet-conseil en communications et</span>
    <span>affaires publiques spécialisé dans le</span>
    <span>secteur de la santé.</span>
  </div>
  <div class="abs hero-cta">En Savior Plus</div>
</section>

<section class="abs pub-head">
  <h2>Publication récentes</h2>
  <p>Lorem Ipsum est simplement du faux texte employé dans la sition et la misen page avant impression.</p>
</section>

<section class="abs pub-list">
  <article class="post" style="top:65px">
    <div class="post-photo" role="img" aria-label="Photo d'un médecin auscultant une patiente" style="background:linear-gradient(90deg,#c9b79a,#e6c27a 60%,#d9c3b0)"></div>
    <div class="post-body">
      <div class="post-title">Titre de la publication</div>
      <div class="post-date">23 juillet 2013</div>
      <p class="post-text">Lorem ipsum dolor sit amet, consectetur adipisicing elit, sed do eiusmod tempor incididunt ut labore et dolore magna aliqua. Ut enim ad minim veniam, quis nostrud exercitation ullamco laboris nisi ut aliquip ex ea commodo consequat. Duis aute irure dolor in reprehenderit in voluptate velit esse cillum dolore eu fugiat nulla pariatur.</p>
      <div class="post-more">Article complet</div>
    </div>
  </article>
  <div class="divider" style="top:303px"></div>

  <article class="post" style="top:336px">
    <div class="post-photo" role="img" aria-label="Photo d'une salle d'opération avec chirurgiens" style="background:linear-gradient(90deg,#9fb2c4,#c9d6e0 55%,#7d93a8)"></div>
    <div class="post-body">
      <div class="post-title">Titre de la publication</div>
      <div class="post-date">23 juillet 2013</div>
      <p class="post-text">Lorem ipsum dolor sit amet, consectetur adipisicing elit, sed do eiusmod tempor incididunt ut labore et dolore magna aliqua. Ut enim ad minim veniam, quis nostrud exercitation ullamco laboris nisi ut aliquip ex ea commodo consequat. Duis aute irure dolor in reprehenderit in voluptate velit esse cillum dolore eu fugiat nulla pariatur.</p>
      <div class="post-more">Article complet</div>
    </div>
  </article>
  <div class="divider" style="top:576px"></div>

  <article class="post" style="top:609px">
    <div class="post-photo" role="img" aria-label="Photo de chercheurs en laboratoire devant un écran" style="background:linear-gradient(90deg,#8fb6cf,#d8e6ee 55%,#b9ccd8)"></div>
    <div class="post-body">
      <div class="post-title">Titre de la publication</div>
      <div class="post-date">23 juillet 2013</div>
      <p class="post-text">Lorem ipsum dolor sit amet, consectetur adipisicing elit, sed do eiusmod tempor incididunt ut labore et dolore magna aliqua. Ut enim ad minim veniam, quis nostrud exercitation ullamco laboris nisi ut aliquip ex ea commodo consequat. Duis aute irure dolor in reprehenderit in voluptate velit esse cillum dolore eu fugiat nulla pariatur.</p>
      <div class="post-more">Article complet</div>
    </div>
  </article>
  <div class="divider" style="top:847px"></div>

  <article class="post" style="top:880px">
    <div class="post-photo" role="img" aria-label="Photo d'une infirmière aidant une patiente âgée" style="background:linear-gradient(90deg,#6b5b4c,#c9b4a3 50%,#a8c9b0)"></div>
    <div class="post-body">
      <div class="post-title">Titre de la publication</div>
      <div class="post-date">23 juillet 2013</div>
      <p class="post-text">Lorem ipsum dolor sit amet, consectetur adipisicing elit, sed do eiusmod tempor incididunt ut labore et dolore magna aliqua. Ut enim ad minim veniam, quis nostrud exercitation ullamco laboris nisi ut aliquip ex ea commodo consequat. Duis aute irure dolor in reprehenderit in voluptate velit esse cillum dolore eu fugiat nulla pariatur.</p>
      <div class="post-more">Article complet</div>
    </div>
  </article>
</section>

<footer class="abs site-footer">
  <h3>Get In Touch</h3>
  <p class="touch-text">Maecenas sed diam eget risus varius. Risus varius blandit sit amet non magna. Duis mollis, est non commodo luctus, nisi erat porttitor ligula, eget lacinia odio sem nec elit. Sed posuere consectetur est at lobortis.</p>

  <div class="newsletter-title">Recevez nos publications</div>
  <div class="field" style="top:203px">Votre nom</div>
  <div class="field" style="top:249px">Votre courriel</div>
  <div class="submit">SUBMIT</div>

  <div class="col-title" style="left:132px">Address</div>
  <p class="col-text" style="left:132px;top:396px">Fusce dapibus, tellus commodo, tortor mauris</p>
  <div class="contact-line" style="top:426px">
    <svg width="9" height="11" viewBox="0 0 9 11"><path d="M4.5 0A4 4 0 0 0 .5 4c0 3 4 7 4 7s4-4 4-7a4 4 0 0 0-4-4z" fill="#f05a5a"/><circle cx="4.5" cy="4" r="1.5" fill="#2b2b2b"/></svg>
    Allée des Tilleuls 27, Morvane</div>
  <div class="contact-line" style="top:450px">
    <svg width="10" height="10" viewBox="0 0 10 10"><path d="M2 0l2 2.5-1.2 1.3a6 6 0 0 0 3.4 3.4L7.5 6 10 8l-1.5 2C4 10 0 6 0 1.5z" fill="#f05a5a"/></svg>
    0248 613 72 90</div>
  <div class="contact-line" style="top:474px">
    <svg width="11" height="8" viewBox="0 0 11 8"><rect width="11" height="8" fill="#f05a5a"/><path d="M0 0l5.5 4.5L11 0" fill="none" stroke="#2b2b2b"/></svg>
    bonjour@brivardweb.net</div>

  <div class="col-title" style="left:426px">Elsewhere</div>
  <p class="col-text" style="left:426px;top:400px;width:280px">Sed posuere consectetur est at lobortis. Morbi leo risus, porta ac consectetur malesuada magna.</p>
  <div class="net-icons" aria-label="Réseaux sociaux">
    <span style="background:#f28c2e"></span><span style="background:#3aa9e0"></span><span style="background:#3b5998"></span><span style="background:#e066a3"></span><span style="background:#e23c4b"></span><span style="background:#8a6a4f"></span><span style="background:#1ab7ea"></span>
  </div>

  <div class="feed-name">Chirpline</div>
  <p class="tweet" style="top:306px">Dolore eu feugiat nulla facilisis at vero eros et accumsan et iusto odio dignissim qui blandit praesent <b>@luptatum zzril delenit augue duis dolore</b></p>
  <p class="tweet" style="top:372px">Dolore eu feugiat nulla facilisis at vero eros et accumsan et iusto odio dignissim qui blandit praesent <b>@luptatum zzril delenit augue duis dolore</b></p>
  <p class="tweet" style="top:440px">Dolore eu feugiat nulla facilisis at vero eros et accumsan et iusto odio dignissim qui blandit praesent <b>@luptatum zzril delenit augue duis dolore</b></p>
</footer>

<div class="abs footer-bottom">© 2013 <strong>Solène Brivard</strong> All rights reserved. Theme by Velandor.</div>

</body>
</html>
```